Law Firm Website

We are a small California based law firm specializing in business, corporate and litigation matters. We need to have our website redesigned. We are looking for a new and fresh look for our site, keeping in mind that we are a law firm.
What we don't want:
**the traditional "gavel" and "scales of justice" look
**anything too crazy
What we do want:
**sophisticated yet modern and fresh corporate look and feel
**samples of websites we really like:
http://www.tarnwellhope.example
http://www.marrowgate.example/
we also like:
http://www.fenwoodastley.example/
http://www.qz.example/
http://www.brenhollow.example/
http://www.pvdn.example
http://www.nqrlaw.example/
The content will be whatever is currently on our website (www.okabelawgroup.example). We will be selecting the winner based on originality and keeping the above requirements in mind. Please note that the photos that you use will be the ones that we will be using, so choose wisely because the photos will make a difference.
Target Market(s)
Corporate clients
Industry/Entity Type
Law Firm
Look and feel

```html
<!DOCTYPE html>
<html lang="en">
<head>
<meta charset="utf-8">
<title>Okabe Law Group, LLP</title>
<link rel="stylesheet" href="https://fonts.googleapis.com/css2?family=Arimo:wght@400;700&family=Open+Sans:wght@400;600&family=Tinos&display=swap">
<style>
:root{
  --white:#ffffff;
  --ink:#111111;
  --text:#3a3a3a;
  --muted:#8a8a8a;
  --brand:#1f6fd1;
  --hero-top:#8d9098;
  --hero-mid:#c8c8c6;
  --hero-low:#6f737c;
  --icon:#5a5a5a;
  --icon-ring:#d6d6d6;
  --btn-light:#f2f3f5;
  --btn-edge:#c9ccd1;
  --footer:#000000;
  --social:#3a3a3a;
}
*{box-sizing:border-box;margin:0;padding:0}
html,body{width:1200px;height:982px;overflow:hidden;background:var(--white)}
body{position:relative;font-family:"Arimo",Arial,sans-serif;color:var(--text)}

.site-header{position:absolute;left:0;top:0;width:1200px;height:120px;background:var(--white)}
.brand{position:absolute;left:71px;top:20px;display:flex;flex-direction:column;align-items:flex-start;gap:8px}
.brand-mark{width:64px;height:64px;background:var(--brand);margin-left:31px}
.brand-name{font-family:"Arimo",Arial,sans-serif;font-weight:700;font-size:14px;color:var(--ink);letter-spacing:-0.2px}
.login{position:absolute;left:1017px;top:16px;width:120px;height:39px;border:1px solid var(--btn-edge);border-radius:3px;background:linear-gradient(#ffffff,#e9eaec);display:flex;align-items:center;gap:14px;padding-left:10px;font-family:"Tinos",serif;font-size:16px;color:var(--ink);box-shadow:0 1px 2px rgba(0,0,0,.15)}
.main-nav{position:absolute;right:65px;top:79px;font-family:"Open Sans",Arial,sans-serif;font-weight:600;font-size:14px;color:var(--ink);display:flex;gap:13px}

.hero{position:absolute;left:0;top:120px;width:1200px;height:459px;background:linear-gradient(180deg,var(--hero-top) 0%,var(--hero-mid) 45%,#b9babb 65%,var(--hero-low) 100%)}
.hero-photo{position:absolute;left:560px;top:0;width:640px;height:459px;background:radial-gradient(ellipse at 62% 95%,rgba(255,255,255,.55),rgba(255,255,255,0) 40%),linear-gradient(180deg,rgba(60,62,70,.15),rgba(40,42,50,.35))}
.hero-title{position:absolute;left:66px;top:104px;font-size:26px;font-weight:400;color:var(--ink);letter-spacing:.3px}
.hero-text{position:absolute;left:69px;top:134px;width:440px;font-size:13px;line-height:24px;color:var(--ink)}
.hero-cta{position:absolute;left:68px;top:278px;width:149px;height:50px;background:var(--white);font-size:20px;color:var(--ink);display:flex;align-items:center;justify-content:center}
.slider-dots{position:absolute;left:69px;top:430px;display:flex;gap:2px}
.slider-dots span{width:13px;height:13px;border-radius:50%;background:rgba(255,255,255,.75)}
.slider-dots span.active{background:var(--white)}

.features{position:absolute;left:0;top:579px;width:1200px;height:272px}
.feature{position:absolute;top:49px;width:330px}
.feature-icon{position:absolute;left:0;top:0;width:73px;height:73px;border-radius:50%;background:var(--icon);border:5px solid var(--icon-ring);display:flex;align-items:center;justify-content:center}
.feature-title{position:absolute;left:93px;top:8px;font-size:20px;color:var(--ink);white-space:nowrap}
.feature-text{position:absolute;left:92px;top:40px;width:230px;font-size:13px;line-height:20px;color:var(--text);text-align:justify}
.feature-more{position:absolute;left:92px;top:115px;width:111px;height:33px}
.feature-more span{position:absolute;left:0;top:0;width:111px;height:33px;display:flex;align-items:center;padding-left:22px;font-size:11px;color:var(--muted);letter-spacing:.2px}

.skyline{position:absolute;left:390px;top:812px;width:483px;height:39px;background:linear-gradient(180deg,rgba(0,0,0,0) 0%,rgba(0,0,0,.55) 55%,#000 100%)}

.site-footer{position:absolute;left:0;top:851px;width:1200px;height:131px;background:var(--footer);color:var(--white)}
.footer-nav{position:absolute;left:67px;top:48px;font-size:13px}
.copyright{position:absolute;left:69px;top:85px;font-size:13px}
.social{position:absolute;left:500px;top:58px;display:flex;gap:13px}
.social span{width:37px;height:37px;border-radius:50%;background:var(--social);border:3px solid #1c1c1c;box-shadow:inset 0 2px 3px rgba(255,255,255,.25)}
.newsletter{position:absolute;left:833px;top:58px;width:303px;height:35px;background:var(--white);border:1px solid #cfcfcf;font-size:13px;color:#666;padding:0 9px;display:flex;align-items:center}
</style>
</head>
<body>

<header class="site-header">
  <div class="brand">
    <span class="brand-mark"></span>
    <span class="brand-name">Okabe Law Group, LLP</span>
  </div>
  <div class="login">
    <svg width="22" height="26" viewBox="0 0 22 26" aria-hidden="true">
      <path d="M5 11V7a6 6 0 0 1 12 0v4" fill="none" stroke="#9a9a9a" stroke-width="2.5"/>
      <rect x="2" y="11" width="18" height="14" rx="2" fill="#b5b5b5"/>
    </svg>
    <span>LOG IN</span>
  </div>
  <nav class="main-nav">
    <span>O NAS</span><span>|</span><span>INDYWIDUALNI</span><span>|</span><span>KORPORACYJNI</span><span>|</span><span>KONTAKT</span>
  </nav>
</header>

<section class="hero">
  <div class="hero-photo" role="img" aria-label="Photograph of a balance scale silhouetted against a cloudy evening sky"></div>
  <h1 class="hero-title">LAW VIVAMUS QUAM</h1>
  <p class="hero-text">Sed ut perspiciatis unde omnis iste natus error sit voluptatem accusantium dolorem que laudantium lorem ipsum totamSed ut perspiciatis unde omnis iste natus error sit voluptatem accusantium dolorem que laudantium lorem ipsum totam</p>
  <div class="hero-cta">Learn More</div>
  <div class="slider-dots"><span></span><span class="active"></span><span class="active"></span></div>
</section>

<section class="features">
  <article class="feature" style="left:68px">
    <div class="feature-icon">
      <svg width="44" height="44" viewBox="0 0 44 44" aria-hidden="true">
        <path d="M22 6 40 15 22 24 4 15Z" fill="#fff"/>
        <path d="M4 22l18 9 18-9M4 29l18 9 18-9" fill="none" stroke="#fff" stroke-width="3"/>
      </svg>
    </div>
    <h2 class="feature-title">Very Flexible</h2>
    <p class="feature-text">Lorem ipsum dolor slo onsec designs tueraliquet Morbi nec In Curabitur nel dolor slo onsec</p>
    <div class="feature-more">
      <svg width="111" height="33" viewBox="0 0 111 33" aria-hidden="true"><path d="M1 1H100L110 16.5 100 32H1Z" fill="var(--btn-light)" stroke="var(--btn-edge)"/></svg>
      <span>LEARN MORE</span>
    </div>
  </article>

  <article class="feature" style="left:442px">
    <div class="feature-icon">
      <svg width="44" height="44" viewBox="0 0 44 44" aria-hidden="true">
        <path d="M22 8V36M14 36h16M8 13h28" stroke="#fff" stroke-width="3" fill="none"/>
        <path d="M4 25h10l-5-10ZM30 25h10l-5-10Z" fill="#fff"/>
      </svg>
    </div>
    <h2 class="feature-title">Vivamus venenatis</h2>
    <p class="feature-text">Lorem ipsum dolor slo onsec designs tueraliquet Morbi nec In Curabitur nel dolor slo onsec</p>
    <div class="feature-more">
      <svg width="111" height="33" viewBox="0 0 111 33" aria-hidden="true"><path d="M1 1H100L110 16.5 100 32H1Z" fill="var(--btn-light)" stroke="var(--btn-edge)"/></svg>
      <span>LEARN MORE</span>
    </div>
  </article>

  <article class="feature" style="left:820px">
    <div class="feature-icon">
      <svg width="44" height="44" viewBox="0 0 44 44" aria-hidden="true">
        <path d="M12 22 22 11M12 22 32 22M12 22 22 33" stroke="#fff" stroke-width="3"/>
        <circle cx="12" cy="22" r="5" fill="var(--icon)" stroke="#fff" stroke-width="3"/>
        <circle cx="24" cy="9" r="5" fill="var(--icon)" stroke="#fff" stroke-width="3"/>
        <circle cx="33" cy="22" r="5" fill="var(--icon)" stroke="#fff" stroke-width="3"/>
        <circle cx="24" cy="35" r="5" fill="var(--icon)" stroke="#fff" stroke-width="3"/>
      </svg>
    </div>
    <h2 class="feature-title">Maecenas fringilla</h2>
    <p class="feature-text">Lorem ipsum dolor slo onsec designs tueraliquet Morbi nec In Curabitur nel dolor slo onsec</p>
    <div class="feature-more">
      <svg width="111" height="33" viewBox="0 0 111 33" aria-hidden="true"><path d="M1 1H100L110 16.5 100 32H1Z" fill="var(--btn-light)" stroke="var(--btn-edge)"/></svg>
      <span>LEARN MORE</span>
    </div>
  </article>
</section>

<div class="skyline" role="img" aria-label="City skyline silhouette rising from the footer"></div>

<footer class="site-footer">
  <nav class="footer-nav">O NAS | INDYWIDUALNI | KORPORACYJNI | KONTAKT</nav>
  <p class="copyright">© 2014&nbsp; Law Centre, All Rights Reserved</p>
  <div class="social"><span></span><span></span><span></span><span></span><span></span></div>
  <div class="newsletter">Sign up to our newsletter</div>
</footer>

</body>
</html>
```